App Design - Career Prep Pal

We require an App Design for our new App called 'Hiring Helper'. This app is essentially an assistant to help Users prepare for job interviews, to help them get hired. <br/><br/>Users who download the App can view common Questions and Answers, save their favourite responses and also view common Interview Tips. <br/><br/>The vision for our App is for Users who are preparing for an interview (1 week before, 1 day before, even 1 hour before), are able to download, view and educate themselves on common questions and responses, and then be confident to land the job. <br/><br/>Our team has developed wireframes to help highlight what each screen should do and include. Please see attached document, which also highlights key requirements for the experience. Feel free to add/remove/edit what you see on these wireframes. Our preference is that you use Adobe XD please.<br/><br/>In terms of design guidelines, we want the experience to be simple, intuitive and 'memorable' to help Users to remember the questions/responses when they are in the interview. <br/><br/>The final design should communicate 'neat and clean professionalism'; we like the design of: jobvista net au<br/><br/>Thank you for reading! Good luck !

Target Market(s)

Professional job seekers

Font styles to use
Sans Serif

Colors

Designer to choose colors to be used in the design.

Requirements
Must have
• Please see my PixelGuild_UX file that I have uploaded
Nice to have
• Could you also please include some ideas on how we can incorporate Advertising into the app screens

```html
<!DOCTYPE html>
<html lang="en">
<head>
<meta charset="utf-8">
<title>Hiring Helper – Interview Tips</title>
<link href="https://fonts.googleapis.com/css2?family=Poppins:wght@400;500;600;700&display=swap" rel="stylesheet">
<style>
  :root {
    --page-bg: #ffffff;
    --screen-bg: #f8f9f9;
    --header-start: #86ff12;
    --header-end: #0af200;
    --header-text: #ffffff;
    --status-text: #1a1a1a;
    --title-text: #1e1e1e;
    --body-text: #222222;
  }
  * { box-sizing: border-box; margin: 0; padding: 0; }
  html, body {
    width: 1200px;
    height: 1200px;
    overflow: hidden;
    background: var(--page-bg);
    font-family: "Poppins", sans-serif;
  }
  .canvas {
    width: 1200px;
    height: 1200px;
    display: flex;
    align-items: center;
    justify-content: center;
  }
  .app-screen {
    width: 582px;
    height: 1106px;
    background: var(--screen-bg);
    border-radius: 40px;
    overflow: hidden;
    box-shadow: 0 0 0 1px #e4e6e6;
  }
  .app-header {
    height: 156px;
    background: linear-gradient(90deg, var(--header-start), var(--header-end));
    position: relative;
  }
  .status-bar {
    height: 50px;
    display: flex;
    align-items: center;
    justify-content: space-between;
    padding: 0 52px 0 46px;
    color: var(--status-text);
    font-weight: 700;
    font-size: 19px;
  }
  .status-icons { display: flex; align-items: center; gap: 10px; }
  .header-bar {
    display: flex;
    align-items: center;
    height: 106px;
    padding-left: 26px;
  }
  .back-button { width: 50px; height: 50px; }
  .app-title {
    flex: 1;
    text-align: center;
    color: var(--header-text);
    font-weight: 700;
    font-size: 39px;
    padding-right: 76px;
    letter-spacing: -0.3px;
  }
  .tips {
    padding: 48px 40px 0;
    color: var(--body-text);
  }
  .tips-title {
    text-align: center;
    font-weight: 600;
    font-size: 27px;
    color: var(--title-text);
    margin-bottom: 40px;
  }
  .tips-list {
    list-style: decimal inside;
    text-align: center;
    font-size: 19.5px;
    line-height: 24px;
    letter-spacing: -0.2px;
  }
  .tips-list li { margin-bottom: 10px; }
</style>
</head>
<body>
<div class="canvas">
  <main class="app-screen">
    <header class="app-header">
      <div class="status-bar">
        <span class="status-time">05:30 AM</span>
        <span class="status-icons">
          <svg width="22" height="18" viewBox="0 0 22 18" aria-hidden="true">
            <rect x="0" y="12" width="3.5" height="6" fill="#1a1a1a"/>
            <rect x="5.5" y="8" width="3.5" height="10" fill="#1a1a1a"/>
            <rect x="11" y="4" width="3.5" height="14" fill="#1a1a1a"/>
            <rect x="16.5" y="0" width="3.5" height="18" fill="#1a1a1a"/>
          </svg>
          <svg width="50" height="22" viewBox="0 0 50 22" aria-hidden="true">
            <rect x="1.5" y="1.5" width="42" height="19" rx="9.5" fill="none" stroke="#1a1a1a" stroke-width="2.5"/>
            <rect x="45" y="7" width="4" height="8" rx="1.5" fill="#1a1a1a"/>
            <text x="22.5" y="16" text-anchor="middle" font-family="Poppins, sans-serif" font-weight="700" font-size="13" fill="#1a1a1a">50</text>
          </svg>
        </span>
      </div>
      <div class="header-bar">
        <svg class="back-button" viewBox="0 0 50 50" aria-label="Back">
          <path d="M44 25 H9 M24 9 L8 25 L24 41" fill="none" stroke="#ffffff" stroke-width="6" stroke-linecap="round" stroke-linejoin="round"/>
        </svg>
        <h1 class="app-title">Hiring Helper</h1>
      </div>
    </header>

    <section class="tips">
      <h2 class="tips-title">Interview Tips</h2>
      <ol class="tips-list">
        <li>Lorem ipsum dolor sit amet,consectetur adipisicing elit. Error quam vero, voluptatibusquaerat minus blanditiis! Odio quo, ratione, magnam quia fuga quae earum! Voluptate totamiure expedita blanditiis nesciunt recusandae.</li>
        <li>Lorem ipsum dolor sit amet,consectetur adipisicing elit. Error quam vero, voluptatibusquaerat minus blanditiis! Odio quo, ratione, magnam quia fuga quae earum! Voluptate totamiure expedita blanditiis nesciunt recusandae.</li>
        <li>Lorem ipsum dolor sit amet,consectetur adipisicing elit. Error quam vero, voluptatibusquaerat minus blanditiis! Odio quo, ratione, magnam quia fuga quae earum! Voluptate totamiure expedita blanditiis nesciunt recusandae.</li>
        <li>Lorem ipsum dolor sit amet,consectetur adipisicing elit. Error quam vero, voluptatibusquaerat minus blanditiis! Odio quo, ratione, magnam quia fuga quae earum! Voluptate totamiure expedita blanditiis nesciunt recusandae.</li>
        <li>Lorem ipsum dolor sit amet,consectetur adipisicing elit. Error quam vero, voluptatibusquaerat minus blanditiis! Odio quo, ratione, magnam quia fuga quae earum! Voluptate totamiure expedita blanditiis nesciunt recusandae.</li>
        <li>Lorem ipsum dolor sit amet,consectetur adipisicing elit. Error quam vero, voluptatibusquaerat minus blanditiis! Odio quo, ratione, magnam.</li>
      </ol>
    </section>
  </main>
</div>
</body>
</html>
```